Export company based in South America (Ecuador) we export flowers, chocolate, and bananas

We need a website that gives our potential clients and introduction into our company and the different types of commodities we export around the world. We are based in Quito, Ecuador so the website should portray the feel of Ecuadorian landscapes within a modern looking website.
At the moment we are exporting roses, chocolate, and bananas so the website should have an intro to our company and then three different areas that describe our three main commodity. The three different sections should explain why each of the products from Ecuador are some of the best in the world in their categories and the benefits of importing the commodity through our company.
Industry/Entity Type
Commodity
Number of Pages Required
4 page

```html
<!DOCTYPE html>
<html lang="en">
<head>
<meta charset="utf-8">
<title>Valdora – Ecuadorian Exports</title>
<link href="https://fonts.googleapis.com/css2?family=Montserrat:wght@500;600&family=Mulish:wght@400;600&family=Barlow:wght@400;500;600&display=swap" rel="stylesheet">
<style>
:root{
  --orange:#f8560a;
  --ink:#2b2b2b;
  --text:#555;
  --white:#fff;
  --grey-bg:#f4f4f4;
  --footer:#1c1c1c;
}
*{box-sizing:border-box;margin:0;padding:0}
html,body{width:1200px;height:3327px;overflow:hidden;background:var(--white)}
body{position:relative;font-family:"Mulish",sans-serif;color:var(--text)}
.abs{position:absolute}
.center{left:0;width:1200px;text-align:center}

/* header */
.site-header{position:absolute;top:0;left:0;width:1200px;height:110px;background:var(--white)}
.brand{position:absolute;left:110px;top:20px;font-family:"Barlow",sans-serif;font-weight:500;font-size:44px;color:var(--orange);letter-spacing:.5px}
.main-nav{position:absolute;top:42px;right:112px;display:flex;gap:31px;font-family:"Montserrat",sans-serif;font-weight:500;font-size:14px;color:#222}
.main-nav .active{color:var(--orange)}

/* hero */
.hero{position:absolute;top:110px;left:0;width:1200px;height:691px;
  border-radius:0 0 50% 50% / 0 0 168px 168px;overflow:hidden;
  background:linear-gradient(100deg,#3b4452 0%,#5b5a63 35%,#7d5f52 65%,#c07a45 88%,#e39448 100%)}
.hero-shade{position:absolute;inset:0;background:rgba(20,20,30,.25)}
.hero h1{position:absolute;top:275px;font-family:"Montserrat",sans-serif;font-weight:600;font-size:57px;color:var(--white);letter-spacing:1px}
.hero p{position:absolute;top:352px;font-size:22px;line-height:34px;color:var(--white)}
.btn{display:inline-block;background:var(--orange);color:var(--white);font-family:"Montserrat",sans-serif;font-weight:500;font-size:16px;text-align:center;border-radius:2px}
.hero .btn{position:absolute;left:534px;top:440px;width:131px;height:46px;line-height:46px}
.hero-arrow{position:absolute;top:294px;width:34px;height:34px}

/* products */
.section-title{font-family:"Montserrat",sans-serif;font-weight:500;font-size:42px;color:var(--ink)}
.section-title span{color:var(--orange)}
.product{position:absolute;top:981px;width:340px;text-align:center}
.product-photo{margin:0 auto;width:236px;height:236px;border-radius:50%;border:1px solid #ddd;padding:6px;background:var(--white);box-shadow:0 0 3px rgba(0,0,0,.1)}
.product-photo div{width:100%;height:100%;border-radius:50%}
.product h3{margin-top:24px;font-family:"Montserrat",sans-serif;font-weight:500;font-size:22px;color:var(--ink);letter-spacing:.5px}
.product p{margin:14px auto 0;width:260px;font-size:14px;line-height:26.5px;color:#555}

/* benefits */
.benefits{position:absolute;top:1438px;left:0;width:1200px;height:467px;background:var(--orange)}
.benefits-photo{position:absolute;left:0;top:0;width:593px;height:467px;background:linear-gradient(160deg,#7a8da8 0%,#b08a80 40%,#e58a4a 60%,#3a5d8a 85%,#2b3d5a 100%)}
.benefits h2{position:absolute;left:624px;top:38px;font-family:"Montserrat",sans-serif;font-weight:500;font-size:44px;color:var(--white)}
.benefits .lead{position:absolute;left:630px;top:110px;width:470px;font-size:16px;line-height:27px;color:var(--white)}
.benefit-icon{position:absolute;left:623px;width:88px;height:88px;border-radius:50%;background:var(--white)}
.benefit-icon svg{position:absolute;left:22px;top:22px}
.benefit h4{position:absolute;left:736px;font-family:"Barlow",sans-serif;font-weight:500;font-size:18px;color:var(--white)}
.benefit p{position:absolute;left:736px;width:360px;font-family:"Barlow",sans-serif;font-size:13.5px;line-height:23px;color:var(--white)}

/* why us */
.why{position:absolute;top:1905px;left:0;width:1200px;height:540px;background:var(--grey-bg)}
.why h2{position:absolute;left:111px;top:92px}
.why p{position:absolute;left:111px;top:166px;width:448px;font-size:14.2px;line-height:29.2px;text-align:justify;color:#555}
.why .btn{position:absolute;left:111px;top:432px;width:144px;height:51px;line-height:51px}
.why-photo{position:absolute;left:615px;top:1983px;width:474px;height:524px;background:linear-gradient(135deg,#c9a77a 0%,#b8b2a6 40%,#8d9296 70%,#6d7378 100%)}

/* testimonials */
.testimonial-text{position:absolute;top:2660px;left:220px;width:760px;text-align:center;font-size:15.5px;line-height:30px;color:#666}
.avatar{position:absolute;left:480px;top:2838px;width:101px;height:101px;border-radius:50%;background:linear-gradient(160deg,#8a6a55,#c79a7a)}
.author{position:absolute;left:601px;top:2864px}
.author strong{display:block;font-family:"Barlow",sans-serif;font-weight:500;font-size:19px;color:var(--orange)}
.author span{display:block;font-family:"Mulish",sans-serif;font-size:15px;color:#333;margin-top:2px}

/* footer */
.site-footer{position:absolute;top:2988px;left:0;width:1200px;height:339px;background:var(--footer)}
.footer-brand{position:absolute;top:36px;font-family:"Barlow",sans-serif;font-weight:500;font-size:64px;color:var(--orange)}
.footer-nav{position:absolute;top:144px;display:flex;justify-content:center;font-family:"Montserrat",sans-serif;font-weight:500;font-size:14px;color:var(--white)}
.footer-nav span.sep{margin:0 27px}
.social{position:absolute;top:196px;width:60px;height:60px;border-radius:50%;border:1px solid #ddd}
.social svg{position:absolute;left:20px;top:22px}
.copyright{position:absolute;top:288px;font-family:"Barlow",sans-serif;font-size:14px;color:var(--white)}
</style>
</head>
<body>

<header class="site-header">
  <div class="brand">Valdora</div>
  <nav class="main-nav">
    <span class="active">HOME</span><span>ABOUT US</span><span>PRODUCTS</span><span>BENEFITS</span><span>WHY CHOOSE US</span><span>CONTACT US</span>
  </nav>
</header>

<section class="hero" role="img" aria-label="Photo of stacked shipping containers and trucks at a port at sunset">
  <div class="hero-shade"></div>
  <h1 class="center">VALDORA</h1>
  <p class="center">Sed ut perspiciatis unde omnis iste natus error sit voluptatem<br>accusantium doloremque laudantium</p>
  <span class="btn">READ MORE</span>
  <svg class="hero-arrow" style="left:59px" viewBox="0 0 34 34"><circle cx="17" cy="17" r="16" fill="none" stroke="#fff" stroke-width="1.5"/><path d="M19 11l-6 6 6 6" fill="none" stroke="#fff" stroke-width="2"/></svg>
  <svg class="hero-arrow" style="left:1105px" viewBox="0 0 34 34"><circle cx="17" cy="17" r="16" fill="none" stroke="#fff" stroke-width="1.5"/><path d="M15 11l6 6-6 6" fill="none" stroke="#fff" stroke-width="2"/></svg>
</section>

<h2 class="section-title abs center" style="top:830px">Our <span>Product</span></h2>
<p class="abs center" style="top:897px;font-size:16.5px;color:#444">Sed ut perspiciatis unde omnis iste natus error sit voluptatem accusantium doloremque</p>

<div class="product" style="left:100px">
  <div class="product-photo"><div role="img" aria-label="Photo of red roses" style="background:radial-gradient(circle,#d0202a,#8a0d14)"></div></div>
  <h3>FLOWERS</h3>
  <p>Sed ut perspiciatis unde omnis iste natus error sit voluptatem accusantium doloremque laudantium, totam</p>
</div>
<div class="product" style="left:436px">
  <div class="product-photo"><div role="img" aria-label="Photo of broken dark chocolate pieces" style="background:radial-gradient(circle,#7a4a35,#3a2420)"></div></div>
  <h3>CHOCOLATE</h3>
  <p>Sed ut perspiciatis unde omnis iste natus error sit voluptatem accusantium doloremque laudantium, totam</p>
</div>
<div class="product" style="left:766px">
  <div class="product-photo"><div role="img" aria-label="Photo of ripe yellow bananas" style="background:radial-gradient(circle,#f8cf2c,#d79a10)"></div></div>
  <h3>BANANAS</h3>
  <p>Sed ut perspiciatis unde omnis iste natus error sit voluptatem accusantium doloremque laudantium, totam</p>
</div>

<section class="benefits">
  <div class="benefits-photo" role="img" aria-label="Photo collage of cargo plane, ship, containers and a hand using a tablet with logistics icons"></div>
  <h2>Our Benifits</h2>
  <p class="lead">Sed ut perspiciatis unde omnis iste natus error sit voluptatem accusantium doloremque laudantium</p>
  <div class="benefit">
    <div class="benefit-icon" style="top:200px"><svg width="44" height="44" viewBox="0 0 44 44" fill="none" stroke="#f8560a" stroke-width="1.8"><rect x="14" y="6" width="24" height="32" rx="2"/><circle cx="22" cy="18" r="5"/><path d="M30 14h5M30 20h5M30 26h5M19 32h16"/><path d="M18 22l-10 12"/></svg></div>
    <h4 style="top:203px">Sed ut perspiciatis unde</h4>
    <p style="top:238px">Nemo enim ipsam voluptatem quia voluptas sit asperna turaut odit aut fugit, sed quia consequuntur</p>
  </div>
  <div class="benefit">
    <div class="benefit-icon" style="top:339px"><svg width="44" height="44" viewBox="0 0 44 44" fill="none" stroke="#f8560a" stroke-width="1.8"><rect x="5" y="13" width="34" height="24" rx="3"/><path d="M16 13V8h12v5M5 23h34M19 21h6v5h-6z"/></svg></div>
    <h4 style="top:342px">Sed ut perspiciatis unde</h4>
    <p style="top:377px">Nemo enim ipsam voluptatem quia voluptas sit asperna turaut odit aut fugit, sed quia consequuntur</p>
  </div>
</section>

<section class="why">
  <h2 class="section-title">Why <span>Choose Us</span></h2>
  <p>Sed ut perspiciatis unde omnis iste natus error sit voluptatem accus antium doloremque laudantium, totam rem aperiam, eaque ipsa quae ab illo inventore veritatis et quasi architecto beatae vitae dicta sunt explicabo. Nemo enim ipsam voluptatem quia voluptas sit aspernatur aut odit aut fugit, sed quia consequuntur magni dolores eos qui ratione voluptatem sequi nesciunt.Neque porro quisquam est, qui dolorem ipsum quia dolor sit amet, consectetur, adipisci velit, sed quia non labore et dolore magnam aliquam quaerat voluptatem.</p>
  <span class="btn">READ MORE</span>
</section>
<div class="why-photo" role="img" aria-label="Photo of two warehouse workers in safety vests checking parcels on a roller conveyor"></div>

<h2 class="section-title abs center" style="top:2580px">Our <span>Testimonials</span></h2>
<p class="testimonial-text">Sed ut perspiciatis unde omnis iste natus error sit voluptatem accusantium doloremque laudantium, totam rem aperiam, eaque ipsa quae ab illo inventore veritatis et quasi architecto beatae vitae dicta sunt explicabo. Nemo enim ipsam voluptatem quia voluptas sit aspernatur aut odit aut fugit, sed quia consequuntur magni dolores eos qui ratione voluptatem sequi nesciunt. Neque porro quisquam est, qui dolorem ipsum quia dolor sit amet, consectetur,&nbsp; incidunt ut labore et dolore magnam aliquam quaerat voluptatem.</p>
<div class="avatar" role="img" aria-label="Customer portrait photo"></div>
<div class="author"><strong>Tomas Reyes</strong><span>posed on 03 mar 2020</span></div>

<footer class="site-footer">
  <div class="footer-brand center">Valdora</div>
  <nav class="footer-nav center">
    <span>HOME</span><span class="sep">|</span><span>ABOUT US</span><span class="sep">|</span><span>PRODUCTS</span><span class="sep">|</span><span>BENEFIT</span><span class="sep">|</span><span>WHY CHOOSE US</span><span class="sep">|</span><span>CONTACT US</span>
  </nav>
  <span class="social" style="left:390px"></span>
  <span class="social" style="left:462px"></span>
  <span class="social" style="left:536px"></span>
  <span class="social" style="left:607px"></span>
  <span class="social" style="left:677px"></span>
  <span class="social" style="left:749px"><svg width="20" height="16" viewBox="0 0 20 16" fill="none" stroke="#fff" stroke-width="1.6"><rect x="1" y="1" width="18" height="14" rx="1.5"/><path d="M1 2l9 7 9-7"/></svg></span>
  <p class="copyright center">© Copyrights 2020-Valdora..All Rights Reserved.</p>
</footer>

</body>
</html>
```